Design for a 4 screens iOS and Android app - "VelaTrakko"

The app allows you to track your car gasoline refill ...
We need a design for the 4 screens of the app:
a) 1 form with 3 fields.
b) 1 simple list view
c) 1 summary view
d) 1 text page
2 "alerts" items are also to be designed.
No specific guidelines, nor logo or whatever.
It will be a free app distributed on iOS and Androïd.
We just want to make it looking nice & very usable for end users.
Target Market(s)
B2C app
Industry/Entity Type
Android

```html
<!DOCTYPE html>
<html lang="en">
<head>
<meta charset="utf-8">
<title>VelaTrakko – About</title>
<link href="https://fonts.googleapis.com/css2?family=Roboto:wght@400;700;900&display=swap" rel="stylesheet">
<style>
  :root {
    --bar-blue: #0088ff;
    --bar-divider: #d6ecff;
    --sky-top: #7cc0e8;
    --sky-mid: #78bae8;
    --sky-bottom: #2466b8;
    --text-white: #ffffff;
  }
  * { margin: 0; padding: 0; box-sizing: border-box; }
  html, body { width: 675px; height: 1200px; overflow: hidden; }
  body {
    font-family: "Roboto", sans-serif;
    color: var(--text-white);
    background: linear-gradient(180deg, var(--sky-top) 0%, var(--sky-mid) 68%, var(--sky-bottom) 100%);
    position: relative;
  }
  .tab-bar {
    display: flex;
    height: 107px;
    background: var(--bar-blue);
  }
  .tab-item {
    flex: 1;
    display: flex;
    align-items: center;
    justify-content: center;
  }
  .tab-item + .tab-item { border-left: 1px solid var(--bar-divider); }
  .tab-item svg { width: 60px; height: 60px; }
  .info-page {
    padding: 0 50px;
  }
  .info-title {
    margin-top: 88px;
    text-align: center;
    font-weight: 700;
    font-size: 31px;
  }
  .info-body {
    margin-top: 28px;
    font-size: 27.2px;
    line-height: 34px;
    text-align: justify;
    hyphens: manual;
  }
  .close-button {
    position: absolute;
    left: 196px;
    top: 934px;
    width: 283px;
    height: 86px;
    border: none;
    border-radius: 22px;
    background: var(--bar-blue);
    color: var(--text-white);
    font-family: "Roboto", sans-serif;
    font-weight: 900;
    font-size: 34px;
  }
</style>
</head>
<body>
  <nav class="tab-bar">
    <div class="tab-item" aria-label="Add refill">
      <svg viewBox="0 0 60 60"><path d="M30 8v44M8 30h44" stroke="#fff" stroke-width="4.5" stroke-linecap="round"/></svg>
    </div>
    <div class="tab-item" aria-label="Refill list">
      <svg viewBox="0 0 64 60"><g fill="#fff"><circle cx="6" cy="9" r="4.5"/><circle cx="6" cy="30" r="4.5"/><circle cx="6" cy="51" r="4.5"/></g><path d="M18 9h42M18 30h42M18 51h42" stroke="#fff" stroke-width="4.5" stroke-linecap="round"/></svg>
    </div>
    <div class="tab-item" aria-label="Summary">
      <svg viewBox="0 0 60 60"><path d="M4 6v48h54" fill="none" stroke="#fff" stroke-width="4.5"/><path d="M10 50V24l8-6 10 12 8-8 16 22z" fill="#fff"/></svg>
    </div>
  </nav>
  <main class="info-page">
    <h1 class="info-title">Lorem ipsum</h1>
    <p class="info-body">Lorem ipsum dolor sit amet, consectetur adipisicing elit, sed do eiusmod tempor inci&shy;didunt ut labore et dolore magna aliqua. Ut enim ad minim veniam, quis nostrud exerci&shy;tation ullamco laboris nisi ut aliquip ex ea commodo consequat. Duis aute irure dolor in reprehenderit in voluptate velit esse cillum dolore eu fugiat nulla pariatur. Excepteur sint occaecat cupidatat non proident, sunt in culpa qui officia deserunt mollit anim id est laborum. Sed ut perspiciatis unde omnis iste natus error sit voluptatem accusantium do&shy;loremque laudantium, totam rem aperiam, eaque ipsa quae ab illo inventore veritatis et quasi architecto beatae vitae dicta sunt ex&shy;plicabo.</p>
  </main>
  <button class="close-button" type="button">Close</button>
</body>
</html>
```